Veranix - Solution provider in business consulting

Veranix is a swiss based company providing solutions for developing markets. The business covers various fields of business consulting, such as supply chain, product costs, quality management and manufacturing management. The Business operates in a efficient, straight and solution oriented manner.
The final design should communicate these characteristics. Asian people as well as as western people shall identify the qualities of the company at first sight.
The customer needs business cards with a simple view but an recognizable design, printed in high quality. Engraved elements such as the globe or simple words are possible.
Available colors are: (RAL)
102/102/102
51/102/102
153/204/153
255/102/51
Font: Calibri

```html
<!DOCTYPE html>
<html lang="en">
<head>
<meta charset="utf-8">
<title>Veranix business cards</title>
<link rel="stylesheet" href="https://fonts.googleapis.com/css2?family=Carlito:wght@400;700&display=swap">
<style>
  :root {
    --page-bg: #3a3633;
    --card-dark: #1c1c1c;
    --card-grey: #666666;
    --text-soft: #b4b4b4;
    --text-muted: #8a8a8a;
    --name-grey: #707070;
    --brand-white: #ffffff;
    --divider: #2e2e2e;
  }
  * { margin: 0; padding: 0; box-sizing: border-box; }
  html, body {
    width: 1200px; height: 844px; overflow: hidden;
    background: var(--page-bg);
    font-family: "Carlito", "Calibri", sans-serif;
  }
  .stage {
    position: relative; width: 1200px; height: 844px;
    display: flex; align-items: center; justify-content: center; gap: 50px;
  }
  .card {
    width: 510px; height: 330px; position: relative;
    box-shadow: 0 12px 30px rgba(0,0,0,.45);
  }
  .card--front { background: var(--card-dark); }
  .card--back {
    background: var(--card-grey);
    display: flex; align-items: center; justify-content: center;
  }
  .brand {
    display: flex; align-items: center; gap: 10px;
    font-weight: 400; letter-spacing: .5px;
  }
  .brand__dot { border-radius: 50%; flex: none; }
  .card--front .brand {
    position: absolute; left: 62px; top: 140px;
    font-size: 44px; color: var(--text-muted);
  }
  .card--front .brand__dot { width: 30px; height: 30px; background: var(--text-muted); }
  .card--back .brand { font-size: 58px; color: var(--brand-white); }
  .card--back .brand__dot { width: 38px; height: 38px; background: var(--brand-white); }
  .divider {
    position: absolute; left: 300px; top: 40px; bottom: 40px;
    width: 1px; background: var(--divider);
  }
  .details {
    position: absolute; left: 324px; top: 52px;
    color: var(--text-soft); font-size: 13.5px; line-height: 1.3;
  }
  .details__name { color: var(--name-grey); font-weight: 700; font-size: 17px; }
  .details__role { margin-bottom: 20px; }
  .details__address { margin-bottom: 20px; }
  .contact { list-style: none; }
  .contact li { display: flex; align-items: center; gap: 10px; height: 18px; }
  .contact svg { width: 11px; height: 11px; fill: none; stroke: var(--text-muted); stroke-width: 1.4; flex: none; }
</style>
</head>
<body>
<main class="stage">
  <section class="card card--front" aria-label="Business card front">
    <div class="brand"><span class="brand__dot"></span>veranix</div>
    <div class="divider"></div>
    <div class="details">
      <p class="details__name">Martin Keller</p>
      <p class="details__role">CEO</p>
      <p class="details__address">Veranix GmbH Lindenweg 14<br>8400 Talbach Switzerland</p>
      <ul class="contact">
        <li><svg viewBox="0 0 12 12"><rect x="3" y="1" width="6" height="10" rx="1"/></svg>+41 79 000 1234</li>
        <li><svg viewBox="0 0 12 12"><path d="M2 2l2.5-.5 1 2.5-1.3 1a6 6 0 0 0 2.8 2.8l1-1.3 2.5 1L10 10C5 10 2 7 2 2z"/></svg>+41 71 000 5678</li>
        <li><svg viewBox="0 0 12 12"><rect x="1" y="2.5" width="10" height="7"/><path d="M1 2.5l5 4 5-4"/></svg>martin.keller@veranix.ch</li>
        <li><svg viewBox="0 0 12 12"><circle cx="6" cy="6" r="4.5"/><path d="M1.5 6h9M6 1.5c-2 2.5-2 6.5 0 9M6 1.5c2 2.5 2 6.5 0 9"/></svg>www.veranix.ch</li>
      </ul>
    </div>
  </section>
  <section class="card card--back" aria-label="Business card back">
    <div class="brand"><span class="brand__dot"></span>veranix</div>
  </section>
</main>
</body>
</html>
```